Tolvik Commercial Cleaning is lookong for a new business card design.

A fresh new design that's professional and stylish. We need a serious upgrade to our business cards. I have included pictures of our existing ones. Our clients include professional individuals and business owners. We woupdblike something professional and upbeat. Please have fun and see what you come uo with.

Target Market(s)

Property managers, business owners, facility managers and other similar professionals

Industry/Entity Type

Janitorial

Contact Information for Business Card

Name, cell, office number, email, web address

Font styles to use
Sans Serif

Colors

Designer to choose colors to be used in the design.

Requirements
Must have
• please use the green color in our logo
Nice to have
• Bar code
Should not have
• Address

```html
<!DOCTYPE html>
<html lang="en">
<head>
<meta charset="utf-8">
<title>Tolvik Commercial Cleaning – Business Card</title>
<link href="https://fonts.googleapis.com/css2?family=Montserrat:wght@400;500;600;700&display=swap" rel="stylesheet">
<style>
  :root {
    --brand-green: #43ae5b;
    --brand-green-light: #5cbb70;
    --ink: #333333;
    --paper: #ffffff;
    --backdrop: #e9e6e1;
  }
  * { margin: 0; padding: 0; box-sizing: border-box; }
  html, body { width: 900px; height: 1200px; overflow: hidden; }
  body {
    background: var(--backdrop);
    font-family: "Montserrat", Arial, sans-serif;
    position: relative;
  }
  .card {
    position: absolute;
    left: 80px;
    width: 742px;
    height: 440px;
    border-radius: 36px;
    overflow: hidden;
  }
  .card--front { top: 132px; background: var(--paper); }
  .card--back { top: 638px; background: var(--brand-green); }

  .wordmark {
    position: absolute;
    left: 0; right: 0;
    text-align: center;
    font-weight: 700;
    white-space: nowrap;
  }
  .card--front .wordmark {
    top: 110px;
    font-size: 40px;
    color: var(--brand-green);
  }
  .card--back .wordmark {
    top: 178px;
    font-size: 44px;
    color: var(--paper);
  }
  .wordmark__badge {
    display: inline-block;
    width: 22px; height: 22px;
    margin-right: 14px;
    background: currentColor;
    vertical-align: 1px;
  }
  .backdrop-name {
    position: absolute;
    left: 30px; top: 80px;
    font-size: 230px;
    font-weight: 700;
    letter-spacing: -4px;
    color: var(--brand-green-light);
    white-space: nowrap;
  }

  .person {
    position: absolute;
    right: 410px;
    top: 322px;
    text-align: right;
  }
  .person__name {
    font-size: 24px;
    font-weight: 700;
    color: var(--brand-green);
    line-height: 1.2;
  }
  .person__title {
    font-size: 15px;
    color: var(--ink);
    margin-top: 4px;
  }
  .divider {
    position: absolute;
    left: 354px; top: 318px;
    width: 2px; height: 60px;
    background: var(--brand-green);
  }
  .contact {
    position: absolute;
    left: 378px; top: 314px;
    list-style: none;
  }
  .contact__item {
    display: flex;
    align-items: center;
    height: 22px;
    font-size: 16px;
    color: var(--ink);
  }
  .contact__icon {
    width: 12px; height: 12px;
    margin-right: 12px;
    fill: var(--brand-green);
  }
</style>
</head>
<body>
  <section class="card card--front">
    <div class="wordmark"><span class="wordmark__badge"></span>Tolvik Commercial Cleaning</div>

    <div class="person">
      <div class="person__name">Mara Ellison</div>
      <div class="person__title">CEO &amp; Founder</div>
    </div>
    <div class="divider"></div>
    <ul class="contact">
      <li class="contact__item">
        <svg class="contact__icon" viewBox="0 0 12 12"><path d="M1 4c0-1.5 2-2.5 5-2.5S11 2.5 11 4v1H8.5V4h-5v1H1z M2.5 6h7l1 5h-9z"/></svg>
        (37) 555-0182
      </li>
      <li class="contact__item">
        <svg class="contact__icon" viewBox="0 0 12 12"><path d="M0 2.5h12v7H0z" /><path d="M0 2.5l6 4 6-4" fill="none" stroke="#fff" stroke-width="1"/></svg>
        mara@tolvikcleaning.com
      </li>
      <li class="contact__item">
        <svg class="contact__icon" viewBox="0 0 12 12"><circle cx="6" cy="6" r="5.5"/><path d="M0.5 6h11M6 0.5c2 2 2 9 0 11M6 0.5c-2 2-2 9 0 11" fill="none" stroke="#fff" stroke-width="0.8"/></svg>
        www.tolvikcleaning.com
      </li>
    </ul>
  </section>

  <section class="card card--back">
    <div class="backdrop-name" aria-hidden="true">Tolvik</div>
    <div class="wordmark"><span class="wordmark__badge"></span>Tolvik Commercial Cleaning</div>
  </section>
</body>
</html>
```